U.S. Popcorn company needs business cards

We are a popcorn company that manufactures popcorn and sells it to grocery stores worldwide. Our theme is "Americana" and our logo is U.S. route 66 which is the most famous highway in the U.S.

We would like the design to be simple and to use both sides. On the back side we would like to see just the logo and website. The front would be normal details

Target Market(s)

Wholesalers, grocers and distributors

Industry/Entity Type

Manufacture

Contact Information for Business Card

Business name: Prairie Lantern Popcorn
Phone: +1 555 308 4726
Email: Dale@prairielanternpopcorn.com
website: www.prairielanternpopcorn.com
Tag Line: "Freshly popped daily"
Name: Dale Whitcombe
Title: Founder/President

Requirements
Must have
• Either this design should be fun or clean and simple. I will let you show me your thougths.
Nice to have
• Anything that ties in the real Hwy Route 66.
• Colors might need to be red, white and blue incorporated.
Should not have
• Not be too busy.

```html
<!DOCTYPE html>
<html lang="en">
<head>
<meta charset="utf-8">
<title>Prairie Lantern Popcorn – Business Cards</title>
<link href="https://fonts.googleapis.com/css2?family=PT+Sans:ital,wght@0,400;0,700;1,400;1,700&display=swap" rel="stylesheet">
<style>
  :root {
    --backdrop: #5b4b3d;
    --card-white: #ffffff;
    --navy: #0b2a6b;
    --flag-red: #e31e24;
    --ink-grey: #4a4a4a;
    --shadow: rgba(0, 0, 0, 0.35);
  }
  * { margin: 0; padding: 0; box-sizing: border-box; }
  html, body {
    width: 1200px;
    height: 987px;
    overflow: hidden;
    background: var(--backdrop);
    font-family: "PT Sans", sans-serif;
  }
  .card {
    position: absolute;
    left: 293px;
    width: 615px;
    height: 351px;
    box-shadow: 0 3px 8px var(--shadow);
    overflow: hidden;
  }
  .card-front { top: 130px; background: var(--card-white); }
  .card-back { top: 506px; background: var(--flag-red); }

  .front-panel {
    position: absolute;
    inset: 0;
    width: 100%;
    height: 100%;
  }
  .front-panel polygon { fill: var(--navy); }

  .brand-name {
    position: absolute;
    left: 385px;
    top: 0;
    width: 230px;
    height: 351px;
    display: flex;
    align-items: center;
    justify-content: center;
    text-align: center;
    color: var(--card-white);
    font-weight: 700;
    font-size: 36px;
    line-height: 1.1;
    text-transform: uppercase;
    padding: 0 12px;
  }

  .contact-block {
    position: absolute;
    left: 33px;
    top: 200px;
  }
  .person-name {
    color: var(--navy);
    font-weight: 700;
    font-size: 23px;
    line-height: 1.1;
  }
  .person-title {
    color: var(--flag-red);
    font-size: 17px;
    margin-top: 1px;
  }
  .contact-list {
    list-style: none;
    margin-top: 14px;
  }
  .contact-list li {
    display: flex;
    align-items: center;
    gap: 9px;
    color: var(--ink-grey);
    font-size: 15px;
    line-height: 24px;
  }
  .contact-list svg { width: 14px; height: 14px; fill: var(--navy); flex: none; }

  .back-brand {
    position: absolute;
    left: 0;
    right: 0;
    top: 110px;
    text-align: center;
    color: var(--card-white);
    font-weight: 700;
    font-size: 34px;
    line-height: 1.1;
    text-transform: uppercase;
  }
  .back-brand .brand-dot {
    display: block;
    width: 14px;
    height: 14px;
    border-radius: 50%;
    background: var(--card-white);
    margin: 0 auto 14px;
  }
  .tagline {
    position: absolute;
    left: 0;
    right: 0;
    top: 297px;
    text-align: center;
    color: var(--card-white);
    font-size: 18px;
    font-weight: 700;
    font-style: italic;
  }
</style>
</head>
<body>

<section class="card card-front" aria-label="Business card front">
  <svg class="front-panel" viewBox="0 0 615 351" preserveAspectRatio="none" aria-hidden="true">
    <polygon points="337,0 615,0 615,351 434,351"/>
  </svg>
  <div class="brand-name">Prairie Lantern Popcorn</div>

  <div class="contact-block">
    <h1 class="person-name">Dale Whitcombe</h1>
    <p class="person-title">Founder/President</p>
    <ul class="contact-list">
      <li>
        <svg viewBox="0 0 24 24" aria-hidden="true"><path d="M6.6 10.8a15.1 15.1 0 0 0 6.6 6.6l2.2-2.2c.3-.3.7-.4 1-.2 1.1.4 2.3.6 3.6.6.6 0 1 .4 1 1V20c0 .6-.4 1-1 1A17 17 0 0 1 3 4c0-.6.4-1 1-1h3.5c.6 0 1 .4 1 1 0 1.3.2 2.5.6 3.6.1.3 0 .7-.2 1z"/></svg>
        +1 555 308 4726
      </li>
      <li>
        <svg viewBox="0 0 24 24" aria-hidden="true"><path d="M2 5h20v14H2z M3.5 6.5 12 13l8.5-6.5" fill="none" stroke="#0b2a6b" stroke-width="2"/></svg>
        Dale@prairielanternpopcorn.com
      </li>
      <li>
        <svg viewBox="0 0 24 24" aria-hidden="true"><circle cx="12" cy="12" r="10"/><path d="M2 12h20M12 2c3 3 3 17 0 20M12 2c-3 3-3 17 0 20" fill="none" stroke="#ffffff" stroke-width="1.5"/></svg>
        www.prairielanternpopcorn.com
      </li>
    </ul>
  </div>
</section>

<section class="card card-back" aria-label="Business card back">
  <div class="back-brand"><span class="brand-dot"></span>Prairie Lantern<br>Popcorn</div>
  <p class="tagline">Freshly popped daily</p>
</section>

</body>
</html>
```